K7 Services business card design contest. Use logo and create a professional layout.

See attached sample. Please sharpen all text and images, don't want any pix-elated content. We are looking for a clean look that quickly provides the information need. Please include our information provided on the sample card. Please feel free to offer any design changes. Please only user the colors provided: #2D3539 & #FFA500. Do not prefer any images other than the K7 Logo

Target Market(s)

Construction, Architects, General Contractors, residential

Industry/Entity Type

Business

Contact Information for Business Card

Company logo, Name, email, fax & phone

Font styles to use
Other font styles liked:
• Josefin Slab

Requirements
Must have
• Name
• Phone & Fax #'s
• address
• Logo
• Website url: www.kq7services.example
Nice to have
• Font Colors #2D3539 & #FFA400
• We prefer a white background.

```html
<!DOCTYPE html>
<html lang="en">
<head>
<meta charset="utf-8">
<title>K7 Services Business Card</title>
<link rel="stylesheet" href="https://fonts.googleapis.com/css2?family=Montserrat:wght@400;500;700&display=swap">
<style>
  :root {
    --ink: #2D3539;
    --accent: #FFA500;
    --paper: #FFFFFF;
    --backdrop: #E4E4E4;
    --muted: #3A4246;
  }
  * { box-sizing: border-box; margin: 0; padding: 0; }
  html, body { width: 1200px; height: 852px; overflow: hidden; }
  body {
    background: var(--backdrop);
    font-family: "Montserrat", Arial, sans-serif;
    color: var(--ink);
    position: relative;
  }
  .card {
    position: absolute;
    width: 525px;
    height: 300px;
    background: var(--paper);
    border-radius: 12px;
    overflow: hidden;
    box-shadow: 0 4px 14px rgba(0,0,0,0.18);
  }
  .card--front { left: 70px; top: 150px; }
  .card--back { left: 605px; top: 400px; }

  .brand {
    display: flex;
    align-items: center;
    gap: 12px;
    font-weight: 700;
    color: var(--ink);
    white-space: nowrap;
  }
  .brand__mark { background: var(--ink); border-radius: 4px; }
  .card--front .brand {
    position: absolute; left: 50%; top: 50%;
    transform: translate(-50%, -50%);
    font-size: 44px;
  }
  .card--front .brand__mark { width: 46px; height: 46px; }
  .card--back .brand {
    position: absolute; right: 36px; top: 34px;
    font-size: 26px; gap: 9px;
  }
  .card--back .brand__mark { width: 28px; height: 28px; border-radius: 3px; }

  .person { position: absolute; left: 30px; top: 98px; }
  .person__name { color: var(--accent); font-size: 19px; font-weight: 400; }
  .person__title { font-size: 12px; margin-top: 4px; color: var(--muted); }

  .contact {
    position: absolute; left: 30px; top: 176px;
    list-style: none; font-size: 12px; line-height: 18px; color: var(--muted);
  }
  .contact li { display: flex; align-items: center; gap: 8px; }
  .contact svg { width: 12px; height: 12px; fill: var(--accent); flex: none; }

  .services {
    position: absolute; right: 0; top: 178px;
    background: var(--ink); color: var(--paper);
    font-size: 12px; letter-spacing: 0.5px;
    padding: 8px 16px;
  }
  .services .sep { color: var(--accent); margin: 0 4px; }

  .band {
    position: absolute; left: 0; right: 0; bottom: 0; height: 8px;
    background: linear-gradient(90deg, var(--accent) 0 82%, var(--ink) 82% 100%);
  }
</style>
</head>
<body>
  <section class="card card--front">
    <div class="brand"><span class="brand__mark"></span>K7 Services</div>
  </section>

  <section class="card card--back">
    <div class="brand"><span class="brand__mark"></span>K7 Services</div>

    <div class="person">
      <p class="person__name">Marcus D. Hollis, MBA</p>
      <p class="person__title">Director of Operations</p>
    </div>

    <ul class="contact">
      <li><svg viewBox="0 0 12 12"><path d="M2 1h3l1 3-1.5 1a6 6 0 0 0 2.5 2.5L8 6l3 1v3a1 1 0 0 1-1 1A9 9 0 0 1 1 2a1 1 0 0 1 1-1z"/></svg>(555) 014 - 7731</li>
      <li><svg viewBox="0 0 12 12"><rect x="1" y="4" width="10" height="7" rx="1"/><rect x="3" y="1" width="6" height="3"/></svg>(555) 017 - 3968</li>
      <li><svg viewBox="0 0 12 12"><circle cx="6" cy="6" r="5"/></svg>www.kq7services.example</li>
      <li class="address">1280 Larkspur Road, Suite</li>
      <li class="address">210-118 Fairview, Georgia, 30000</li>
    </ul>

    <div class="services">DRONE<span class="sep">|</span>WEBCAM<span class="sep">|</span>VIDEO</div>
    <div class="band"></div>
  </section>
</body>
</html>
```